Kelvara Pane Works Business Card

We need a business card design that is suitable for a Glazing Business. We Specialize in Repairing broken windows and doors and are a 24hr on call service. We manufacture Shower screens, Fly screens, Wardrobe doors, Security doors and grilles + mirrors. We stock a variety of mesh including Standard mesh, Pet resistant mesh, Tressmet & Clearweft. We would like to use a combination of Light Blue, Dark Blue, Black & White with perhaps a picture of glass breaking.

Industry/Entity Type

Business

Contact Information for Business Card

Narooma Glass Service60B Glasshouse Rocks RdNarooma NSW 2546PH / FAX - 02 44765210MOB - 0419682350 Andrewemail - kelvarapane@fenmail.example

Font styles to use
Serif

Colors
34a7d8
0255a3
ffffff

Requirements
Must have
• logo with picture of broken or cracked glass

```html
<!DOCTYPE html>
<html lang="en">
<head>
<meta charset="utf-8">
<title>Kelvara Pane Works – Business Card</title>
<link rel="stylesheet" href="https://fonts.googleapis.com/css2?family=Cormorant+Garamond:wght@500;600&display=swap">
<style>
  :root {
    --light-blue: #34a7d8;
    --dark-blue: #0255a3;
    --navy: #224a86;
    --white: #ffffff;
    --backdrop: #e6e8eb;
  }
  * { margin: 0; padding: 0; box-sizing: border-box; }
  html, body {
    width: 1200px;
    height: 873px;
    overflow: hidden;
    background: var(--backdrop);
    font-family: "Cormorant Garamond", Georgia, serif;
  }
  .card {
    position: absolute;
    left: 370px;
    top: 66px;
    width: 460px;
    height: 740px;
    background: var(--white);
    box-shadow: 0 6px 24px rgba(0, 0, 0, 0.18);
    overflow: hidden;
  }
  .card__shapes {
    position: absolute;
    inset: 0;
  }
  .brand {
    position: absolute;
    left: 44px;
    top: 120px;
    display: flex;
    align-items: center;
    gap: 22px;
  }
  .brand__mark {
    width: 74px;
    height: 74px;
    border: 3px solid var(--dark-blue);
    flex: none;
  }
  .brand__name {
    color: var(--light-blue);
    font-weight: 600;
    font-size: 40px;
    line-height: 1.02;
  }
  .phones {
    position: absolute;
    left: 36px;
    top: 400px;
    list-style: none;
    color: var(--white);
    font-size: 21px;
    font-weight: 500;
    line-height: 32px;
  }
  .phones li { display: flex; align-items: center; gap: 14px; }
  .icon { width: 16px; height: 16px; flex: none; }
  .address {
    position: absolute;
    left: 248px;
    top: 470px;
    display: flex;
    gap: 10px;
    color: var(--white);
    font-size: 20px;
    font-weight: 500;
    line-height: 24px;
  }
  .address .icon { margin-top: 26px; }
  .email {
    position: absolute;
    left: 0;
    right: 0;
    top: 652px;
    text-align: center;
    color: var(--white);
    font-size: 24px;
    font-weight: 500;
  }
</style>
</head>
<body>
  <article class="card">
    <svg class="card__shapes" viewBox="0 0 460 740" width="460" height="740" aria-hidden="true">
      <polygon fill="var(--navy)" points="0,385 225,385 285,250 460,250 460,540 0,540"/>
      <polygon fill="var(--light-blue)" points="205,455 460,455 460,530 360,530 300,578 240,530"/>
      <polygon fill="var(--white)" points="0,540 240,540 300,588 360,540 460,540 460,604 0,604"/>
      <rect fill="var(--navy)" x="0" y="604" width="460" height="136"/>
      <rect fill="var(--white)" x="0" y="618" width="460" height="3"/>
    </svg>

    <header class="brand">
      <span class="brand__mark"></span>
      <h1 class="brand__name">Kelvara<br>Pane Works</h1>
    </header>

    <ul class="phones">
      <li>
        <svg class="icon" viewBox="0 0 16 16"><circle cx="8" cy="8" r="7" fill="none" stroke="#fff" stroke-width="1.4"/><rect x="5.5" y="3.5" width="5" height="9" rx="1" fill="#fff"/></svg>
        0419682350
      </li>
      <li>
        <svg class="icon" viewBox="0 0 16 16"><circle cx="8" cy="8" r="7" fill="none" stroke="#fff" stroke-width="1.4"/><path d="M4.5 6.5c0-1.5 7-1.5 7 0v1h-2v-1h-3v1h-2zM5 8.5h6v3H5z" fill="#fff"/></svg>
        02 48931067
      </li>
    </ul>

    <address class="address">
      <svg class="icon" viewBox="0 0 16 16"><path d="M8 2 1 8h2v6h4v-4h2v4h4V8h2z" fill="#fff"/></svg>
      <span>17C Tindale Ridge Rd,<br>Kelvara NSW 2538</span>
    </address>

    <p class="email">kelvarapane@fenmail.example</p>
  </article>
</body>
</html>
```